Request for Business Card Design

Hi. My name is Marlene, I am looking for a new business card design for my company, Quarrow Signal Instruments, LLC. I really like the design you did for Tarsel Venture and was hoping you could do something similar using our full logo and our mark. I am also open to any raised texture design using our mark. I have attached our full logo, which would need to be somewhere on the card, as well as the mark in both outline and full form, as well as our brand colors / guide. The card does not have to be white, as long as our logo and mark appear. I actually like darker colored business cards more, but am open to all options. If you are interested in working with me, please let me know. We would also take the business card design into letterhead design if you can do that.

```html
<!DOCTYPE html>
<html lang="en">
<head>
<meta charset="utf-8">
<title>Quarrow Signal Instruments – Business Card</title>
<link href="https://fonts.googleapis.com/css2?family=Open+Sans:wght@400;600;700&display=swap" rel="stylesheet">
<style>
  :root {
    --stage: #222223;
    --card: #3e3e40;
    --edge: #1b9ac6;
    --accent: #1a9cd0;
    --ink-light: #ffffff;
    --ink-deep: #1c1c1e;
  }
  * { margin: 0; padding: 0; box-sizing: border-box; }
  html, body { width: 1200px; height: 780px; overflow: hidden; background: var(--stage); }
  body { position: relative; font-family: "Open Sans", Arial, sans-serif; }

  .card {
    position: absolute;
    width: 560px;
    height: 320px;
    background: var(--card);
    border-radius: 22px;
    border: 3px solid var(--edge);
    overflow: hidden;
  }
  .card--back { left: 60px; top: 60px; }
  .card--front { left: 580px; top: 400px; }

  /* Back: centred brand name */
  .brand {
    display: flex;
    align-items: center;
    gap: 16px;
  }
  .brand__dot {
    border-radius: 50%;
    flex: none;
  }
  .brand__name {
    font-weight: 700;
    text-transform: uppercase;
    letter-spacing: 1px;
    line-height: 1.05;
  }
  .card--back .brand {
    position: absolute;
    left: 0; right: 0; top: 0; bottom: 0;
    justify-content: center;
  }
  .card--back .brand__dot { width: 58px; height: 58px; background: var(--ink-deep); }
  .card--back .brand__name { font-size: 30px; color: var(--ink-deep); }

  /* Front */
  .card--front .brand { position: absolute; left: 26px; top: 26px; gap: 12px; }
  .card--front .brand__dot { width: 38px; height: 38px; background: var(--accent); }
  .card--front .brand__name { font-size: 19px; color: var(--ink-light); }

  .person {
    position: absolute;
    right: 34px;
    top: 78px;
    text-align: right;
  }
  .person__name { font-size: 34px; font-weight: 700; color: var(--accent); line-height: 1; }
  .person__role { font-size: 15px; color: var(--ink-light); margin-top: 2px; }
  .person-bar {
    position: absolute;
    right: 0;
    top: 76px;
    width: 20px;
    height: 52px;
    background: var(--accent);
  }

  .address {
    position: absolute;
    left: 70px;
    top: 140px;
    font-size: 14.5px;
    color: var(--ink-light);
    line-height: 1.35;
  }

  .contacts {
    position: absolute;
    left: 70px;
    top: 208px;
    list-style: none;
    font-size: 14.5px;
    color: var(--ink-light);
  }
  .contacts li {
    display: flex;
    align-items: center;
    gap: 10px;
    height: 21px;
  }
  .contacts svg { width: 14px; height: 14px; flex: none; }
  .icon { fill: none; stroke: var(--accent); stroke-width: 1.8; stroke-linecap: round; stroke-linejoin: round; }
</style>
</head>
<body>

  <section class="card card--back" aria-label="Card back">
    <div class="brand">
      <span class="brand__dot"></span>
      <span class="brand__name">Quarrow Signal<br>Instruments</span>
    </div>
  </section>

  <section class="card card--front" aria-label="Card front">
    <div class="brand">
      <span class="brand__dot"></span>
      <span class="brand__name">Quarrow Signal<br>Instruments</span>
    </div>

    <div class="person">
      <p class="person__name">Marlene</p>
      <p class="person__role">Director</p>
    </div>
    <span class="person-bar"></span>

    <address class="address" style="font-style:normal">
      1180 Fenwick Park Road<br>
      Aldermoor, CO 80719
    </address>

    <ul class="contacts">
      <li>
        <svg viewBox="0 0 16 16" aria-hidden="true"><path class="icon" d="M4 2l2.5 3-1.5 1.5a8 8 0 0 0 4.5 4.5L11 9.5l3 2.5-1.5 2A10 10 0 0 1 2 3.5z"/></svg>
        +001 555 218 4407
      </li>
      <li>
        <svg viewBox="0 0 16 16" aria-hidden="true"><rect class="icon" x="2" y="6" width="12" height="8" rx="1"/><path class="icon" d="M5 6V2h6v4M5 10h6"/></svg>
        +001 555 218 4472
      </li>
      <li>
        <svg viewBox="0 0 16 16" aria-hidden="true"><circle class="icon" cx="8" cy="8" r="6"/><path class="icon" d="M2 8h12M8 2c2.5 3 2.5 9 0 12M8 2c-2.5 3-2.5 9 0 12"/></svg>
        www.quarrowsignal.com
      </li>
      <li>
        <svg viewBox="0 0 16 16" aria-hidden="true"><rect class="icon" x="2" y="4" width="12" height="9" rx="1"/><path class="icon" d="M2 5l6 4.5L14 5"/></svg>
        info@quarrowsignal.com
      </li>
    </ul>
  </section>

</body>
</html>
```